Business Card design for law firm = Brightvale Australia

We are seeking a new design for our business cards.
We are keeping our logo, which is attached.
We need space for
Name
Title
Address is , which is
Level 7
214 Marlowe Street
Sydney NSW 2047
Phone :
Mobile :
Fax :
Email :
DX :
website www.brightvale-example.com.au

Industry/Entity Type

Law Firm / Banking and Finance

Contact Information for Business Card

We are seeking a new design for our business cards. We are keeping our logo. We need space for Name Title Address is Level 7 214 Marlowe Street Sydney NSW 2047 Phone Mobile Fax Email DX website www.brightvale-example.com.au

Colors
0054AA
0677BA
7BADD7
CADEEF
E8F1F8

Requirements
Must have
• see our website for general feel www.brightvale-example.com.au

```html
<!DOCTYPE html>
<html lang="en">
<head>
<meta charset="utf-8">
<title>Brightvale Business Card</title>
<link href="https://fonts.googleapis.com/css2?family=Crimson+Pro:wght@400;600&family=Open+Sans:wght@400&display=swap" rel="stylesheet">
<style>
  :root {
    --ink-blue: #0054AA;
    --mid-blue: #0677BA;
    --soft-blue: #2A9FD6;
    --text-grey: #3a3a3a;
    --card: #ffffff;
    --backdrop: #dcdde0;
  }
  * { margin: 0; padding: 0; box-sizing: border-box; }
  html, body { width: 1200px; height: 800px; overflow: hidden; }
  body {
    background: var(--backdrop);
    font-family: "Crimson Pro", "Times New Roman", serif;
    position: relative;
  }
  .card {
    position: absolute;
    top: 241px;
    width: 520px;
    height: 318px;
    background: var(--card);
    box-shadow: 0 6px 18px rgba(0,0,0,0.12);
  }
  .card--front { left: 50px; }
  .card--back { left: 630px; }

  .brand__name {
    font-family: "Crimson Pro", "Times New Roman", serif;
    font-weight: 400;
    color: var(--ink-blue);
    font-size: 44px;
    line-height: 1;
  }
  .tagline {
    font-family: "Open Sans", Arial, sans-serif;
    color: var(--soft-blue);
    font-size: 13px;
    letter-spacing: 1px;
    margin-top: 6px;
  }

  /* front */
  .front-lockup { position: absolute; right: 60px; bottom: 54px; width: 260px; }
  .web-bar {
    margin-top: 8px;
    background: var(--ink-blue);
    color: #fff;
    font-size: 15px;
    letter-spacing: 0.5px;
    padding: 2px 8px;
    display: inline-block;
  }

  /* back */
  .person { position: absolute; left: 32px; top: 30px; }
  .person__name { color: var(--ink-blue); font-weight: 600; font-style: italic; font-size: 19px; }
  .person__title { color: var(--text-grey); font-size: 13px; }
  .person__mobile { display: flex; align-items: center; gap: 6px; color: var(--text-grey); font-size: 13px; margin-top: 3px; }

  .back-lockup { position: absolute; right: 40px; top: 40px; width: 240px; }
  .back-lockup .brand__name { font-size: 38px; }
  .back-lockup .tagline { font-size: 11.5px; }
  .rule { height: 1px; background: var(--mid-blue); margin-top: 10px; width: 230px; }

  .contact { position: absolute; left: 246px; top: 174px; color: var(--text-grey); font-size: 13.5px; line-height: 1.3; }
  .contact__row { display: flex; align-items: center; gap: 7px; }
  .contact__address { margin-top: 8px; }
  .contact__dx { color: var(--mid-blue); }
  .icon { width: 11px; height: 11px; flex: none; }
</style>
</head>
<body>

<section class="card card--front" aria-label="Card front">
  <div class="front-lockup">
    <p class="brand__name">Brightvale</p>
    <p class="tagline">considered legal partnership</p>
    <span class="web-bar">www.brightvale-example.com.au</span>
  </div>
</section>

<section class="card card--back" aria-label="Card back">
  <div class="person">
    <p class="person__name">Sam Whitford</p>
    <p class="person__title">Managing Director</p>
    <p class="person__mobile">
      <svg class="icon" viewBox="0 0 12 12" aria-hidden="true"><rect x="3" y="0.5" width="6" height="11" rx="1" fill="none" stroke="#0677BA"/><line x1="5" y1="10" x2="7" y2="10" stroke="#0677BA"/></svg>
      22 4810 3376
    </p>
  </div>

  <div class="back-lockup">
    <p class="brand__name">Brightvale</p>
    <p class="tagline">considered legal partnership</p>
    <div class="rule"></div>
  </div>

  <div class="contact">
    <p class="contact__row">
      <svg class="icon" viewBox="0 0 12 12" aria-hidden="true"><path d="M1 4 Q6 0 11 4 L9 6 L7 4.5 L5 4.5 L3 6 Z M2 7 H10 V11 H2 Z" fill="#0677BA"/></svg>
      02 4810 0190
    </p>
    <p class="contact__row">
      <svg class="icon" viewBox="0 0 12 12" aria-hidden="true"><rect x="1" y="5" width="10" height="6" fill="#0677BA"/><rect x="3" y="1" width="6" height="4" fill="none" stroke="#0677BA"/></svg>
      02 4810 0191
    </p>
    <p class="contact__row">
      <svg class="icon" viewBox="0 0 12 12" aria-hidden="true"><rect x="1" y="2.5" width="10" height="7" fill="#0677BA"/><path d="M1 2.5 L6 7 L11 2.5" fill="none" stroke="#fff"/></svg>
      enquiries@brightvale-example.com.au
    </p>
    <div class="contact__address">
      <p class="contact__row">
        <svg class="icon" viewBox="0 0 12 12" aria-hidden="true"><path d="M6 11.5 C2 7 2 5 2 4.5 A4 4 0 0 1 10 4.5 C10 5 10 7 6 11.5 Z" fill="#0677BA"/><circle cx="6" cy="4.5" r="1.5" fill="#fff"/></svg>
        Level 7, 214 Marlowe Street
      </p>
      <p>Sydney NSW 2047</p>
      <p class="contact__dx">DX 312 Sydney</p>
    </div>
  </div>
</section>

</body>
</html>
```